New business card/stationary for a consulting company

I am looking for a clean and very professional looking business card for my consulting company as well as corresponding stationary. I am uploading our logo. I like simple and powerful for the feel. No graphics but I am open on everything else. Below is my contact information but would like the final to be in a version I can add my employees information into and print. Thank you.

Daniel Whitcombe
dan@ferncliffadvisory.com
2870 North 9th Avenue, Summit Floor, Elm Ridge, Illinois 60531
www.ferncliffadvisory.com

Industry/Entity Type

Consulting

Contact Information for Business Card

Daniel Whitcombe
dan@ferncliffadvisory.com
www.ferncliffadvisory.com

Font styles to use
Serif
Sans Serif

Requirements
Must have
• Our logo and the business card details.
Nice to have
• our website www.ferncliffadvisory.com

```html
<!DOCTYPE html>
<html lang="en">
<head>
<meta charset="utf-8">
<title>Ferncliff Advisory — Business Card</title>
<link rel="stylesheet" href="https://fonts.googleapis.com/css2?family=Questrial&family=Ubuntu:wght@400&display=swap">
<style>
  :root {
    --backdrop: #525252;
    --navy: #02026a;
    --white: #ffffff;
    --ink: #2b2b2b;
    --faint: #ececec;
  }
  * { margin: 0; padding: 0; box-sizing: border-box; }
  html, body { width: 1200px; height: 900px; overflow: hidden; }
  body { background: var(--backdrop); position: relative; font-family: "Questrial", sans-serif; }

  .card { position: absolute; top: 306px; width: 440px; height: 271px; overflow: hidden; }
  .card--front { left: 149px; background: var(--white); }
  .card--back { left: 608px; background: var(--navy); }

  .front-band { position: absolute; left: 0; top: 0; width: 100%; height: 86px; background: var(--navy); }
  .band-name {
    position: absolute; left: 23px; top: 32px;
    font-family: "Questrial", sans-serif; font-size: 21px; letter-spacing: 0.2px;
    color: var(--white); white-space: nowrap;
  }
  .band-mark { position: absolute; left: 350px; top: 29px; width: 57px; height: 57px; background: var(--white); }

  .holder-name {
    position: absolute; left: 24px; top: 123px;
    font-family: "Questrial", sans-serif; font-size: 14px; letter-spacing: 0.6px; color: var(--navy);
  }
  .address {
    position: absolute; left: 24px; top: 152px;
    font-family: "Ubuntu", sans-serif; font-size: 11.5px; line-height: 15.5px; color: var(--ink);
  }
  .contact-list { position: absolute; left: 23px; top: 209px; list-style: none;
    font-family: "Ubuntu", sans-serif; font-size: 11.5px; line-height: 16px; color: var(--ink); }
  .contact-list li { display: flex; align-items: center; gap: 4px; }
  .contact-list svg { width: 9px; height: 9px; fill: var(--navy); }

  .faint-name {
    position: absolute; right: 22px; top: 184px;
    font-family: "Questrial", sans-serif; font-size: 40px; color: var(--faint); white-space: nowrap;
  }

  .back-mark { position: absolute; left: 194px; top: 92px; width: 52px; height: 52px; background: var(--white); }
  .back-name {
    position: absolute; left: 0; width: 100%; top: 155px; text-align: center;
    font-family: "Questrial", sans-serif; font-size: 25px; letter-spacing: 0.3px; color: var(--white);
  }
</style>
</head>
<body>
  <section class="card card--front">
    <header class="front-band">
      <span class="band-name">FERNCLIFF ADVISORY</span>
      <span class="band-mark"></span>
    </header>
    <span class="faint-name" aria-hidden="true">FERNCLIFF</span>
    <h1 class="holder-name">DANIEL WHITCOMBE</h1>
    <p class="address">2870 North 9th Avenue,<br>Summit Floor, Elm Ridge,<br>Illinois 60531</p>
    <ul class="contact-list">
      <li>
        <svg viewBox="0 0 10 10" aria-hidden="true"><path d="M0 2h10v6H0z M0 2l5 3.5L10 2" fill="var(--navy)"/><path d="M0.6 2.6L5 5.6 9.4 2.6" stroke="#fff" stroke-width="0.9" fill="none"/></svg>
        dan@ferncliffadvisory.com
      </li>
      <li>
        <svg viewBox="0 0 10 10" aria-hidden="true"><circle cx="5" cy="5" r="4.6"/><path d="M2 4c1 0 1.5 1 2.5 0.5S4 2 5 1.8M6 8.5c0-1 1-1.5 1.8-1.6" stroke="#fff" stroke-width="0.9" fill="none"/></svg>
        www.ferncliffadvisory.com
      </li>
    </ul>
  </section>

  <section class="card card--back">
    <span class="back-mark"></span>
    <p class="back-name">FERNCLIFF ADVISORY</p>
  </section>
</body>
</html>
```